Local Flower Farm Needs Business Card Design

I need business cards designed for a flower farm based in Eudora, Kansas.
Business Info:
We are a local cut flower farm located in Eudora, Kansas, founded by Corinne Haldwick. What started as a passion for agriculture and search for more joy in daily life has blossomed into a small business dedicated to providing the community with beautiful, fresh, and sustainable flowers. We specialize in local, seasonal blooms, ensuring that every petal reflects the care and dedication we pour into our craft. Our mission is to deliver the highest quality flowers directly to our customers through local farmers markets and to florists who share our commitment to sustainability. Join us in celebrating the beauty of nature, one bloom at a time!
Contact Details:
Corinne Haldwick
Owner
Phone 913-555-0147
Facebook: Rosalind Thorpe Gardens
Instagram: @RosalindThorpeGardens
Website: RosalindThorpeGardens.example
Target Market(s)
Wholesale to Florists and Direct to Consumer via Farmers Market
Industry/Entity Type
Florist, Farm
Contact Information for Business Card
Name, Contact Info, Logo
Look and feel
Each slider illustrates characteristics of the customer's brand and the style your logo design should communicate.

```html
<!DOCTYPE html>
<html lang="en">
<head>
<meta charset="utf-8">
<title>Rosalind Thorpe Gardens — Business Card</title>
<link rel="stylesheet" href="https://fonts.googleapis.com/css2?family=Montserrat:wght@400;500;700&display=swap">
<style>
  :root {
    --ink: #0f2e2f;
    --paper: #ffffff;
    --stage: #e8e5e0;
    --rule: #6f7777;
  }
  html, body {
    margin: 0;
    padding: 0;
    width: 900px;
    height: 1200px;
    overflow: hidden;
    background: var(--stage);
    font-family: "Montserrat", Arial, sans-serif;
    color: var(--ink);
  }
  .canvas { position: relative; width: 900px; height: 1200px; }

  .card {
    position: absolute;
    background: var(--paper);
    border-radius: 22px;
    overflow: hidden;
  }
  .card--front { left: 80px; top: 131px; width: 742px; height: 440px; }
  .card--back  { left: 78px; top: 638px; width: 744px; height: 440px; }

  /* brand badge: one plain circle with the business name */
  .badge {
    position: absolute;
    border: 1.5px solid var(--rule);
    border-radius: 50%;
    display: flex;
    align-items: center;
    justify-content: center;
    text-align: center;
    box-sizing: border-box;
  }
  .badge__name {
    font-weight: 700;
    color: var(--ink);
    text-transform: uppercase;
    letter-spacing: 0.04em;
    line-height: 1.12;
  }
  .card--front .badge { left: 33px; top: 38px; width: 226px; height: 226px; }
  .card--front .badge__name { font-size: 25px; }
  .card--back .badge { left: 212px; top: 82px; width: 320px; height: 320px; }
  .card--back .badge__name { font-size: 37px; }

  .holder { position: absolute; right: 49px; top: 44px; text-align: right; }
  .holder__name { margin: 0; font-size: 26px; font-weight: 700; letter-spacing: 0.005em; line-height: 1.2; }
  .holder__role { margin: 1px 0 0; font-size: 16px; font-weight: 400; }

  .brand-mark {
    position: absolute;
    left: 468px; top: 218px; width: 250px;
    font-weight: 700;
    font-size: 43px;
    line-height: 1.08;
    text-transform: uppercase;
    letter-spacing: 0.01em;
    text-align: center;
    color: var(--ink);
  }

  .contact-band { position: absolute; left: 0; top: 304px; width: 450px; height: 136px; }
  .contact-list {
    position: absolute; left: 36px; top: 320px;
    margin: 0; padding: 0; list-style: none;
    color: var(--paper); font-size: 16px; font-weight: 400;
  }
  .contact-list li { display: flex; align-items: center; height: 26.5px; }
  .contact-list svg { width: 15px; height: 15px; margin-right: 9px; flex: none; }
</style>
</head>
<body>
<div class="canvas">

  <section class="card card--front" aria-label="Business card front">
    <div class="badge"><span class="badge__name">Rosalind<br>Thorpe<br>Gardens</span></div>

    <div class="holder">
      <h1 class="holder__name">Corinne Haldwick</h1>
      <p class="holder__role">Owner</p>
    </div>

    <div class="brand-mark">Rosalind<br>Thorpe<br>Gardens</div>

    <svg class="contact-band" viewBox="0 0 450 136" preserveAspectRatio="none" aria-hidden="true">
      <polygon points="0,0 272,0 450,136 0,136" fill="var(--ink)"/>
    </svg>

    <ul class="contact-list">
      <li>
        <svg viewBox="0 0 24 24" aria-hidden="true"><path fill="#fff" d="M6.6 10.8a15.1 15.1 0 0 0 6.6 6.6l2.2-2.2a1 1 0 0 1 1-.25 11.4 11.4 0 0 0 3.6.57 1 1 0 0 1 1 1V20a1 1 0 0 1-1 1A17 17 0 0 1 3 4a1 1 0 0 1 1-1h3.5a1 1 0 0 1 1 1c0 1.25.2 2.45.57 3.57a1 1 0 0 1-.25 1z"/></svg>
        913-555-0147
      </li>
      <li>
        <svg viewBox="0 0 24 24" aria-hidden="true"><circle cx="12" cy="12" r="10" fill="#fff"/></svg>
        Rosalind Thorpe Gardens
      </li>
      <li>
        <svg viewBox="0 0 24 24" aria-hidden="true"><rect x="3" y="3" width="18" height="18" fill="#fff"/></svg>
        @RosalindThorpeGardens
      </li>
      <li>
        <svg viewBox="0 0 24 24" aria-hidden="true"><g fill="none" stroke="#fff" stroke-width="2"><circle cx="12" cy="12" r="9.5"/><ellipse cx="12" cy="12" rx="4" ry="9.5"/><path d="M2.5 12h19"/></g></svg>
        www.RosalindThorpeGardens.example
      </li>
    </ul>
  </section>

  <section class="card card--back" aria-label="Business card back">
    <div class="badge"><span class="badge__name">Rosalind<br>Thorpe<br>Gardens</span></div>
  </section>

</div>
</body>
</html>
```